Book cover for book about Climate Change

Looking for a clean, bold, and attractive cover for a mass-market paperback (5.5"x 8.5") about solving the climate change problem. Title is either "Where the Rivers Meet” or A Harbor Made of Glass” (your choice), subtitle is "A practical field guide to mending the weather — so that the young ones after us inherit steady seasons and open skies," author is Lorne Whitcombe. Thinking that it *might* feature an image of Earth (or a portion thereof) and its very thin layer of atmosphere -- but STRONGLY encourage other ideas too!

Requirements
Nice to have
• Keep it positive — NOT scary doom-and-gloom

```html
<!DOCTYPE html>
<html lang="en">
<head>
<meta charset="utf-8">
<title>A Harbor Made of Glass — Book Cover</title>
<link rel="stylesheet" href="https://fonts.googleapis.com/css2?family=Bebas+Neue&family=Poppins:wght@500&display=swap">
<style>
  :root {
    --backdrop-top: #f4f4f4;
    --backdrop-bottom: #c9c9c9;
    --cover-dark: #0b1418;
    --sky-teal: #2f4f58;
    --halo-orange: #c8744a;
    --halo-sand: #b49a86;
    --band-light: #4dbdd4;
    --band-deep: #0a6a85;
    --ink-white: #ffffff;
    --globe-light: #6d7fa3;
    --globe-mid: #3e4f7e;
    --globe-deep: #26325c;
  }
  * { margin: 0; padding: 0; box-sizing: border-box; }
  html, body { width: 1200px; height: 1200px; overflow: hidden; }
  body {
    background: linear-gradient(180deg, var(--backdrop-top), var(--backdrop-bottom));
    position: relative;
  }
  .cover {
    position: absolute;
    left: 182px; top: 29px;
    width: 835px; height: 1140px;
    overflow: hidden;
    background: var(--cover-dark);
    box-shadow: 0 2px 8px rgba(0,0,0,0.25);
  }
  .cover-photo {
    position: absolute; inset: 0;
    background:
      radial-gradient(circle at 50% 42%, var(--sky-teal) 0 38%, var(--halo-sand) 46%, var(--halo-orange) 52%, #3d4f55 60%, #1c2a30 75%),
      var(--cover-dark);
  }
  .cover-photo::after {
    content: ""; position: absolute; left: 0; right: 0; bottom: 0; height: 300px;
    background: linear-gradient(180deg, rgba(11,20,24,0) 0%, var(--cover-dark) 40%);
  }
  .globe {
    position: absolute;
    left: 212px; top: 210px;
    width: 450px; height: 450px;
    border-radius: 50%;
    background: radial-gradient(circle at 45% 40%, var(--globe-light) 0%, var(--globe-mid) 60%, var(--globe-deep) 100%);
    box-shadow: 0 0 18px rgba(0,0,0,0.5);
  }
  .title {
    font-family: "Bebas Neue", "Oswald", sans-serif;
    font-weight: 400;
    color: var(--ink-white);
  }
  .title-main, .title-sub {
    position: absolute; left: 0; right: 0;
    text-align: center;
    line-height: 1;
  }
  .title-main { top: 28px; font-size: 142px; }
  .title-sub { top: 153px; font-size: 76px; }
  .subtitle-band {
    position: absolute; left: 0; right: 0; top: 739px; height: 162px;
    background: linear-gradient(90deg, var(--band-light), var(--band-deep) 50%, var(--band-light));
    opacity: 0.92;
    display: flex; align-items: center; justify-content: center;
  }
  .subtitle {
    font-family: "Poppins", sans-serif;
    font-weight: 500;
    font-size: 20px;
    line-height: 36px;
    color: var(--ink-white);
    text-transform: uppercase;
    text-align: center;
    letter-spacing: -0.2px;
  }
  .author {
    position: absolute; left: 0; right: 0; top: 986px;
    text-align: center;
    font-family: "Bebas Neue", "Oswald", sans-serif;
    font-size: 86px;
    line-height: 1;
    color: var(--ink-white);
    letter-spacing: 1px;
  }
</style>
</head>
<body>
  <div class="cover">
    <div class="cover-photo" role="img" aria-label="Photograph of a hand silhouette raised against a blurred teal sky ringed by a warm orange halo"></div>
    <div class="globe" role="img" aria-label="Photograph of planet Earth seen from space, balanced on the raised hand"></div>
    <h1 class="title">
      <span class="title-main">A HARBOR</span>
      <span class="title-sub">MADE OF GLASS</span>
    </h1>
    <div class="subtitle-band">
      <p class="subtitle">A practical field guide to mending the weather<br>so that the young ones after us inherit<br>steady seasons and open skies</p>
    </div>
    <p class="author">LORNE WHITCOMBE</p>
  </div>
</body>
</html>
```